Business card design for international hub site

I need a business card design with the logo attached. Although the site is for the teenage audience (it is about the high school graduation ball, the Prom), the business card is for professional use to be given to professional contacts (B2B), such as suppliers and partners, so it needs to look professional (but also girly, glamours and clean).

Target Market(s)

B2B

Industry/Entity Type

Media

Colors
eea4c8
f9d9e8
e667a6
9d9d9d
1b1b1b

Requirements
Must have
• Space for Name, Tile, Address, Phone, email and website.
Should not have
• Photo

```html
<!DOCTYPE html>
<html lang="en">
<head>
<meta charset="utf-8">
<title>The Gala Hive – Business Cards</title>
<link rel="stylesheet" href="https://fonts.googleapis.com/css2?family=Arimo:wght@400;700&family=Cormorant+Garamond:wght@500&display=swap">
<style>
  :root {
    --stage: #1b1b1b;
    --pink-deep: #d4187f;
    --pink-mid: #e667a6;
    --pink-soft: #eea4c8;
    --pink-blush: #f9d9e8;
    --ink-light: #ffffff;
    --grey: #9d9d9d;
  }
  * { box-sizing: border-box; margin: 0; padding: 0; }
  html, body {
    width: 1200px; height: 997px; overflow: hidden;
    background: var(--stage);
    font-family: "Arimo", Arial, sans-serif;
  }
  .stage { position: relative; width: 1200px; height: 997px; }
  .card {
    position: absolute; left: 280px;
    width: 640px; height: 366px;
    border-radius: 22px; overflow: hidden;
    box-shadow: 0 12px 30px rgba(0,0,0,.55);
  }
  .card--front { top: 90px; }
  .card--back { top: 540px; }
  .card__texture {
    position: absolute; inset: 0;
    background:
      radial-gradient(circle at 30% 25%, var(--pink-mid) 0%, transparent 55%),
      radial-gradient(circle at 75% 80%, var(--pink-soft) 0%, transparent 50%),
      linear-gradient(135deg, var(--pink-deep), #e0409a 55%, var(--pink-deep));
  }
  .brand-name {
    position: absolute; left: 0; right: 0;
    text-align: center;
    font-family: "Cormorant Garamond", Georgia, serif;
    font-weight: 500; font-size: 46px; letter-spacing: 1px;
    color: var(--pink-blush);
  }
  .card--front .brand-name { top: 150px; }
  .card--back .brand-name { top: 56px; }
  .person {
    position: absolute; right: 44px; top: 168px; text-align: right;
    color: var(--ink-light);
  }
  .person__name { font-weight: 700; font-size: 21px; letter-spacing: .5px; }
  .person__title { font-size: 14px; margin-top: 3px; color: var(--pink-blush); }
  .person__web { font-weight: 700; font-size: 16px; margin-top: 14px; }
  .contact {
    position: absolute; left: 36px; bottom: 28px;
    list-style: none; color: var(--ink-light); font-size: 15px; line-height: 1.25;
  }
  .contact li { display: flex; align-items: flex-start; gap: 10px; margin-top: 6px; }
  .contact svg { flex: none; width: 16px; height: 16px; margin-top: 1px; }
</style>
</head>
<body>
<main class="stage">
  <section class="card card--front">
    <div class="card__texture" role="img" aria-label="Pink glitter texture with soft sparkle highlights"></div>
    <div class="brand-name">The Gala Hive</div>
  </section>

  <section class="card card--back">
    <div class="card__texture" role="img" aria-label="Pink glitter texture with soft sparkle highlights"></div>
    <div class="brand-name">The Gala Hive</div>
    <div class="person">
      <div class="person__name">DAN WHITLEY</div>
      <div class="person__title">Marketing Director</div>
      <div class="person__web">www.lumenpath.com</div>
    </div>
    <ul class="contact">
      <li>
        <svg viewBox="0 0 16 16"><circle cx="8" cy="8" r="8" fill="#fff"/><path d="M5 4.5l1.6-.3.9 2-1 .8a6 6 0 0 0 2.5 2.5l.8-1 2 .9-.3 1.6c-3.5.3-6.8-3-6.5-6.5z" fill="#d4187f"/></svg>
        <span>(800) 555-0142</span>
      </li>
      <li>
        <svg viewBox="0 0 16 16"><circle cx="8" cy="8" r="8" fill="#fff"/><path d="M5 4.5l1.6-.3.9 2-1 .8a6 6 0 0 0 2.5 2.5l.8-1 2 .9-.3 1.6c-3.5.3-6.8-3-6.5-6.5z" fill="#d4187f"/></svg>
        <span>(706) 555-0183</span>
      </li>
      <li>
        <svg viewBox="0 0 16 16"><circle cx="8" cy="8" r="8" fill="#fff"/><rect x="4" y="5.5" width="8" height="5.5" fill="none" stroke="#d4187f" stroke-width="1.2"/><path d="M4 5.5l4 3 4-3" fill="none" stroke="#d4187f" stroke-width="1.2"/></svg>
        <span>dwhitley@lumenpath.com</span>
      </li>
      <li>
        <svg viewBox="0 0 16 16"><circle cx="8" cy="8" r="8" fill="#fff"/><path d="M8 3.5a3 3 0 0 1 3 3c0 2.2-3 5.5-3 5.5s-3-3.3-3-5.5a3 3 0 0 1 3-3z" fill="#d4187f"/><circle cx="8" cy="6.5" r="1" fill="#fff"/></svg>
        <span>480 Meadow Court Lane, 3rd Floor<br>Riverton, GA 30000</span>
      </li>
    </ul>
  </section>
</main>
</body>
</html>
```